The Brookhaven Sessions - Concert Series Website Design

I've recently decided to launch a concert series in my living room and would love a website to use to promote the series. I'm looking for a simple Wix design that I could take over once it's complete. I'll provide the logo for which I'd like the website to utilize the color scheme.

Target Market(s)

Music lovers in Denver

Industry/Entity Type

Music

Coding

Coded - Design and coding required

Number of Pages Required

2 page

Font styles to use
Script

Requirements
Must have
• 2 pages - one for concert goers to see the schedule and rsvp, and one for artists about the booking process

```html
<!DOCTYPE html>
<html lang="en">
<head>
<meta charset="utf-8">
<title>The Brookhaven Sessions</title>
<link href="https://fonts.googleapis.com/css2?family=Outfit:wght@400;500;600;700&display=swap" rel="stylesheet">
<style>
:root{
  --orange:#f9a94d;
  --orange-btn:#fbb866;
  --plum:#2a0a52;
  --plum-deep:#220743;
  --ink:#3a165a;
  --text:#4a4a4a;
  --muted:#7a7a7a;
  --line:#e9e4ee;
  --white:#ffffff;
}
*{box-sizing:border-box;margin:0;padding:0}
html,body{width:1200px;height:3569px;overflow:hidden}
body{position:relative;background:var(--white);font-family:"Outfit",sans-serif;color:var(--text)}
.abs{position:absolute}
.btn{position:absolute;display:flex;align-items:center;justify-content:center;background:var(--orange-btn);color:var(--ink);font-size:14px;font-weight:500;text-transform:uppercase;border-radius:5px;letter-spacing:.2px}

/* header */
.site-header{position:absolute;left:0;top:0;width:1200px;height:78px;background:var(--white);z-index:2}
.brand-badge{position:absolute;left:111px;top:17px;width:102px;height:119px;background:var(--plum);border-radius:12px 12px 51px 51px;z-index:3;display:flex;flex-direction:column;align-items:center;justify-content:center;gap:8px}
.brand-badge .dot{width:22px;height:22px;border-radius:50%;background:var(--orange)}
.brand-badge span{color:var(--white);font-size:11px;font-weight:500;text-align:center;line-height:1.15;text-transform:uppercase}
.nav a{position:absolute;top:31px;font-size:14px;font-weight:500;color:#222;text-decoration:none;text-transform:uppercase}
.nav a.active{color:var(--orange)}
.contact-btn{position:absolute;left:984px;top:22px;width:104px;height:33px;border:1px solid var(--orange);border-radius:5px;font-size:12.5px;color:var(--ink);display:flex;align-items:center;justify-content:center;font-weight:500}

/* hero */
.hero{position:absolute;left:0;top:78px;width:1200px;height:462px;
  background:radial-gradient(circle at 1080px 70px,rgba(255,190,100,.75),transparent 170px),
  radial-gradient(ellipse at 700px 260px,rgba(190,110,50,.55),transparent 380px),
  linear-gradient(180deg,#3a2a2a 0%,#2a1d1a 45%,#140d0b 100%)}
.hero h1{position:absolute;left:111px;top:122px;font-size:33px;line-height:51px;font-weight:700;color:var(--white);text-transform:uppercase;letter-spacing:-.5px}
.hero h1 em{font-style:normal;color:var(--orange)}
.hero p{position:absolute;left:111px;top:236px;width:540px;font-size:16px;line-height:35px;color:var(--white)}
.play{position:absolute;left:902px;top:205px;width:50px;height:50px;border-radius:50%;background:var(--white);display:flex;align-items:center;justify-content:center}

/* section titles */
.title{position:absolute;font-size:30px;font-weight:600;color:var(--orange);text-transform:uppercase;letter-spacing:-.6px;display:flex;align-items:center;gap:16px;white-space:nowrap}
.title i{display:block;width:38px;height:2px;background:var(--plum)}
.title.light i{background:var(--white)}

/* form */
.field{position:absolute;height:47px;border:1px solid #999;border-radius:3px;display:flex;align-items:center;justify-content:space-between;padding:0 18px;font-size:13.5px;color:#222;text-transform:uppercase}
.field svg{flex:none}

/* cards */
.card{position:absolute;top:1129px;width:312px;height:458px;border:1px solid var(--line);border-radius:8px;box-shadow:0 2px 8px rgba(40,10,80,.05);background:var(--white)}
.card .photo{position:absolute;left:13px;top:15px;width:286px;height:175px;border-radius:6px}
.card .date{position:absolute;left:28px;top:224px;font-size:14.5px;color:#666;display:flex;align-items:center;gap:12px}
.card .desc{position:absolute;left:28px;top:264px;width:256px;font-size:14.5px;line-height:29.5px;color:#777;text-align:justify}
.card h3{position:absolute;left:25px;top:367px;font-size:16.5px;font-weight:600;color:var(--ink);text-transform:uppercase;letter-spacing:-.3px}
.card h4{position:absolute;left:25px;top:401px;font-size:13.5px;font-weight:500;color:#555;text-transform:uppercase}

/* experience */
.experience{position:absolute;left:0;top:1674px;width:1200px;height:511px;background:linear-gradient(120deg,var(--plum-deep),#2c0a55 60%,#300c5c)}
.experience p{position:absolute;left:112px;top:120px;width:976px;text-align:center;font-size:16.5px;line-height:34.5px;color:var(--white)}

/* about */
.about p{position:absolute;left:112px;width:561px;font-size:16px;line-height:34.5px;color:#444;text-align:justify}
.call-label{position:absolute;left:860px;top:3084px;font-size:14px;font-weight:500;color:var(--orange);text-transform:uppercase}
.call-num{position:absolute;left:860px;top:3117px;font-size:22px;color:#333}

/* footer */
.site-footer{position:absolute;left:0;top:3237px;width:1200px;height:332px;background:linear-gradient(120deg,var(--plum-deep),#2d0a58)}
.footer-brand{position:absolute;left:114px;top:61px;display:flex;align-items:center;gap:14px;color:var(--white);font-size:27px;line-height:1;font-weight:400;text-transform:uppercase}
.footer-brand .dot{width:70px;height:70px;border-radius:50%;background:var(--orange);flex:none}
.site-footer small{position:absolute;left:114px;font-size:13.5px;color:var(--white);text-transform:uppercase}
.site-footer small em{font-style:normal;color:var(--orange)}
.social{position:absolute;top:254px;width:25px;height:25px;border:1.5px solid var(--white);border-radius:50%}
.footer-col h5{position:absolute;top:60px;font-size:17px;font-weight:600;color:var(--orange);text-transform:uppercase;letter-spacing:-.3px}
.footer-col .bar{position:absolute;top:98px;width:30px;height:2px;background:var(--orange)}
.footer-col a{position:absolute;font-size:14px;color:var(--white);text-decoration:none;text-transform:uppercase}
.signup{position:absolute;left:829px;top:135px;width:256px;height:47px;border:1px solid rgba(255,255,255,.55);border-radius:4px;display:flex;align-items:center;padding-left:15px;font-size:13.5px;color:rgba(255,255,255,.6);text-transform:uppercase}
</style>
</head>
<body>

<header class="site-header">
  <nav class="nav">
    <a class="active" href="#" style="left:631px">Home</a>
    <a href="#" style="left:700px">Concerts</a>
    <a href="#" style="left:807px">For Artists</a>
  </nav>
  <div class="contact-btn">CONTACT US</div>
</header>
<div class="brand-badge"><div class="dot"></div><span>The Brookhaven<br>Sessions</span></div>

<section class="hero">
  <div role="img" aria-label="Photo of an intimate living-room concert with a guitarist and singer by candlelight, mountains seen through the window" style="position:absolute;inset:0"></div>
  <h1><em>Where Music Meets</em> Living<br>Room <em>Magic</em></h1>
  <p>A curated living-room concert series featuring exceptional independent artists in an unforgettable intimate setting.</p>
  <div class="btn" style="left:111px;top:335px;width:187px;height:42px">View Full Schedule</div>
  <div class="play"><svg width="16" height="18" viewBox="0 0 16 18"><path d="M2 1l13 8-13 8z" fill="#111"/></svg></div>
</section>

<!-- reserve -->
<div class="title" style="left:394px;top:615px"><i></i>Reserve Your Seat<i></i></div>
<div class="field" style="left:133px;top:704px;width:452px">Full Name</div>
<div class="field" style="left:614px;top:704px;width:452px">Email Address</div>
<div class="field" style="left:133px;top:784px;width:452px">Select Session<svg width="8" height="5"><path d="M0 0h8L4 5z" fill="#222"/></svg></div>
<div class="field" style="left:614px;top:784px;width:452px">Number of Guests<svg width="8" height="5"><path d="M0 0h8L4 5z" fill="#222"/></svg></div>
<div class="btn" style="left:511px;top:884px;width:178px;height:42px">Reserve My Seat</div>

<!-- upcoming -->
<div class="title" style="left:111px;top:1000px">Upcoming Sessions<i></i></div>
<div class="abs" style="left:111px;top:1058px;font-size:16.5px;color:#333">New sessions are announced regularly.</div>
<div class="btn" style="left:901px;top:1021px;width:187px;height:42px">View More Sessions</div>

<article class="card" style="left:111px">
  <div class="photo" role="img" aria-label="Photo of a cozy music room with a piano and guitars" style="background:linear-gradient(135deg,#2b1d2a,#6a3a2a 55%,#1c1420)"></div>
  <div class="date"><svg width="14" height="13"><rect x="1" y="2" width="12" height="10" fill="none" stroke="#f9a94d"/><path d="M1 5h12M4 1v2M10 1v2" stroke="#f9a94d"/></svg>APRIL 18, 2026 &nbsp;| &nbsp;7:30 PM</div>
  <p class="desc">A Denver favorite known for haunting vocals and intimate acoustic arrangements</p>
  <h3>Ivy Lane &amp; The Still Water</h3>
  <h4>Americana / Singer-Songwriter</h4>
</article>
<article class="card" style="left:443px">
  <div class="photo" role="img" aria-label="Photo of a musician playing acoustic guitar at home" style="background:linear-gradient(135deg,#e8e2da,#c9b8a6 55%,#8a7a6c)"></div>
  <div class="date"><svg width="14" height="13"><rect x="1" y="2" width="12" height="10" fill="none" stroke="#f9a94d"/><path d="M1 5h12M4 1v2M10 1v2" stroke="#f9a94d"/></svg>MAY 9, 2026 &nbsp;| &nbsp;8:00 PM</div>
  <p class="desc">Touring nationally, Owen brings warm, road-worn songwriting and rich guitar work to the Brookhaven</p>
  <h3>Owen Calder</h3>
  <h4>Americana / Singer-Songwriter</h4>
</article>
<article class="card" style="left:776px">
  <div class="photo" role="img" aria-label="Photo of hands playing an electric bass" style="background:linear-gradient(135deg,#111,#3a2a20 55%,#1a1410)"></div>
  <div class="date"><svg width="14" height="13"><rect x="1" y="2" width="12" height="10" fill="none" stroke="#f9a94d"/><path d="M1 5h12M4 1v2M10 1v2" stroke="#f9a94d"/></svg>JUNE 6, 2026 &nbsp;| &nbsp;7:00 PM</div>
  <p class="desc" style="text-align:left">Ethereal textures and intimate vocals create a mesmerizing live experience perfect for fans of atmospheric indie</p>
  <h3>Nova &amp; The Fireflies</h3>
  <h4>Dream Pop / Indie</h4>
</article>

<!-- experience -->
<section class="experience">
  <div class="title light" style="left:416px;top:55px"><i></i>The Experience<i></i></div>
  <p>The Brookhaven Sessions is designed for those who believe live music should be felt, not just heard. Each performance takes place in an intimate living-room setting where artists and audience share the same space, creating a connection that traditional venues rarely achieve. With limited seating, warm acoustics, and carefully curated talent, every session feels personal and immersive.</p>
  <div class="btn" style="left:532px;top:254px;width:136px;height:41px">Learn More</div>
</section>
<div class="abs" role="img" aria-label="Photo of a singer with a microphone and a drummer behind her" style="left:112px;top:2038px;width:976px;height:347px;border-radius:8px;background:linear-gradient(100deg,#5a3a22,#b07a4a 40%,#d8b08a 70%,#a07060)"></div>

<!-- about -->
<section class="about">
  <div class="title" style="left:112px;top:2462px">About The Series<i></i></div>
  <p style="top:2520px">The Brookhaven Sessions is an intimate living-room concert series based in Denver, created to bring music back to its most powerful form — personal, present, and deeply felt. Each session features carefully curated independent artists performing in a warm, attentive listening environment where every note matters.</p>
  <p style="top:2703px">Designed for true music lovers, the series offers a rare alternative to noisy venues and crowded clubs.</p>
  <div class="btn" style="left:112px;top:2802px;width:128px;height:41px">Learn More</div>
  <div class="abs" role="img" aria-label="Photo of musicians recording with keyboard and guitars in a studio" style="left:112px;top:2900px;width:561px;height:250px;border-radius:8px;background:linear-gradient(135deg,#e6e0d8,#a89a8c 45%,#d8a850 70%,#5a4a40)"></div>
  <div class="abs" role="img" aria-label="Photo of a woman singing with an acoustic guitar in a candlelit room" style="left:732px;top:2472px;width:356px;height:574px;border-radius:8px;background:linear-gradient(160deg,#2a2020,#7a4a2a 45%,#a05a3a 65%,#2a1a14)"></div>
  <svg class="abs" style="left:797px;top:3093px" width="42" height="42" viewBox="0 0 42 42" fill="none" stroke="#f9a94d" stroke-width="1.6">
    <circle cx="20" cy="22" r="14"/>
    <path d="M14 16c0 8 5 13 12 13l2-4-4-2-2 2c-2-1-4-3-5-5l2-2-2-4z"/>
    <path d="M28 4h10v7h-6l-3 3v-3h-1z"/>
  </svg>
  <div class="call-label">Call Us Today:</div>
  <div class="call-num">(555) 013-2468</div>
</section>

<!-- footer -->
<footer class="site-footer">
  <div class="footer-brand"><div class="dot"></div><span>The<br>Brookhaven<br>Sessions</span></div>
  <small style="top:174px">© 2026 <em>The Brookhaven Sessions.</em></small>
  <small style="top:206px">All Rights Reserved</small>
  <div class="social" style="left:115px"></div>
  <div class="social" style="left:147px"></div>
  <div class="social" style="left:180px"></div>
  <div class="social" style="left:212px"></div>
  <div class="footer-col">
    <h5 style="left:547px">Explore</h5><div class="bar" style="left:549px"></div>
    <a href="#" style="left:548px;top:128px">Home</a>
    <a href="#" style="left:548px;top:168px">Concerts</a>
    <a href="#" style="left:548px;top:207px">For Artists</a>
    <a href="#" style="left:548px;top:246px">RSVP</a>
  </div>
  <div class="footer-col">
    <h5 style="left:827px">Stay In The Glow</h5><div class="bar" style="left:829px"></div>
  </div>
  <div class="signup">Email Signup</div>
  <div class="btn" style="left:829px;top:209px;width:127px;height:39px;font-size:13px">Subscribe Us</div>
</footer>

</body>
</html>
```